UX Design for Analytics Web Application

http://velqoranthe.com/
We are tech & consulting company with analytics products (web applications), located at Rio de Janeiro, Brazil.

We are searching a partner do develop UX for our products, i.e, aesthetics, usability, HTML/CSS.

Currently we have a product suite and the goal is to make a pilot re-design project with one of our products.

The product of interest is interactive webapp that aims at data analysis, significantly different from blogs, e-commerce or landing pages.

We do have a software development team but we lack an UX & HTML expert. Currently we use Bootstrap templates but the results are insatisfatory.

So, the project scope is, to develop the arts (UX, aesthetics, etc) along with the code/mockup (HTML/CSS) for one of our product (3 pages).

This is a pilot project and there's potential to rehire for our other products. Code quality is of importance.

More details and specification can be found in attached files.

Target Market(s)

Executives, managers & consultants

Industry/Entity Type

It Company

Coding

Coded - Design and coding required

Number of Pages Required

3 page

Font styles to use
Sans Serif

Requirements
Must have
• (see attached files, prefer the pptx version))
• -Responsive
Nice to have
• (see attached files, prefer the pptx version)
Should not have
• -Avoid Green, Red and Yellow colors. They have a meaning of good, bad and average in our products.

```html
<!DOCTYPE html>
<html lang="en">
<head>
<meta charset="utf-8">
<title>Velqoranthe – Process Dashboard</title>
<link href="https://fonts.googleapis.com/css2?family=Montserrat:wght@400;500;600;700&display=swap" rel="stylesheet">
<style>
:root{
  --navy:#1a5e9e;
  --blue:#2f86c4;
  --sky:#3a9fe6;
  --sky-light:#a8ccec;
  --coral:#f4513f;
  --orange:#f26522;
  --panel:#f2f2f2;
  --line:#d6d6d6;
  --ink:#333;
  --muted:#888;
  --footer:#2a84c0;
}
*{box-sizing:border-box;margin:0;padding:0}
html,body{width:1200px;height:772px;overflow:hidden}
body{font-family:"Montserrat",Arial,sans-serif;background:#fff;color:var(--ink);position:relative}
a{text-decoration:none}

.site-header{position:absolute;left:0;top:0;width:1200px;height:79px;background:#fff;box-shadow:0 2px 4px rgba(0,0,0,.08)}
.brand{position:absolute;left:99px;top:22px;display:flex;align-items:center;gap:10px}
.brand-dot{width:34px;height:34px;border-radius:50%;background:var(--navy)}
.brand-name{font-size:30px;font-weight:700;color:#444;letter-spacing:-.5px}
.header-icons{position:absolute;left:980px;top:30px;display:flex;gap:30px}
.header-icons svg{width:20px;height:20px;fill:var(--sky)}

.stats-panel{position:absolute;left:105px;top:115px;width:398px;height:232px;background:var(--panel);border:1px solid var(--line);overflow:hidden}
.stats-deco{position:absolute;left:20px;top:20px;width:230px;height:200px;background:radial-gradient(circle at 40% 55%,rgba(240,200,200,.45),rgba(215,220,225,.35) 45%,rgba(242,242,242,0) 70%)}
.stats-title{position:absolute;left:23px;top:58px;font-size:21px;font-weight:600;color:var(--navy)}
.donut{position:absolute;left:266px;top:18px;width:104px;height:104px}
.donut-label{position:absolute;left:266px;top:18px;width:104px;height:104px;line-height:104px;text-align:center;font-size:19px;font-weight:700;color:#444}
.stat-lines{position:absolute;left:22px;top:140px;font-size:13.5px;font-weight:600;line-height:27.5px;color:#333}
.stat-bar{position:absolute;left:265px;height:12px}
.stat-bar span{position:absolute;left:100%;margin-left:5px;top:-1px;font-size:10px;font-weight:700}
.bar-spent{top:144px;width:93px;background:var(--orange)}
.bar-gap{top:170px;width:46px;background:var(--sky-light)}
.bar-negotiated{top:199px;width:34px;background:var(--blue)}

.feed-panel{position:absolute;left:105px;top:371px;width:398px;height:325px;background:var(--panel);border:1px solid var(--line)}
.feed-head{height:64px;background:var(--coral);display:flex;align-items:center;justify-content:center;gap:18px;color:#fff;font-size:26px;font-weight:600}
.feed-head svg{width:28px;height:22px;fill:#fff}
.feed-icon{position:absolute;left:24px;width:32px;height:32px}
.feed-text{position:absolute;left:82px;width:300px;font-size:14.5px;line-height:25px;color:#444}
.see-all{position:absolute;right:12px;bottom:8px;color:var(--coral);font-size:15px;text-decoration:underline}

.toolbar{position:absolute;left:517px;top:115px;width:575px;height:46px;background:var(--sky);display:flex;align-items:center;justify-content:space-around;color:#fff;font-size:14px;font-weight:600}
.toolbar span::before{content:"";display:inline-block;width:8px;height:8px;margin-right:6px;background:#fff;border-radius:2px;vertical-align:1px}

.cards-panel{position:absolute;left:517px;top:173px;width:575px;height:523px;background:var(--panel);border:1px solid var(--line)}
.process-card{position:absolute;width:249px;height:186px;background:#fff;border:1px solid #ccc;border-radius:4px;box-shadow:0 1px 3px rgba(0,0,0,.12);overflow:hidden}
.card-media{position:relative;height:66px;background:linear-gradient(180deg,#3d3a36 0%,#5a6f86 55%,#2f3f52 100%)}
.card-title{position:absolute;left:0;right:0;top:37px;text-align:center;color:#fff;font-size:15px;font-weight:700;text-shadow:0 1px 2px rgba(0,0,0,.5)}
.card-flag{position:absolute;right:0;top:0;width:44px;height:44px}
.card-body{position:relative;height:120px}
.card-arrow{position:absolute;left:24px;top:20px;width:16px;height:16px;fill:var(--blue)}
.card-amount{position:absolute;left:50px;top:16px;font-size:19px;font-weight:500;color:var(--blue);line-height:22px}
.card-amount small{display:block;font-size:15px;font-weight:500}
.card-badge{position:absolute;left:173px;top:10px;width:48px;height:48px;border-radius:50%;border:4px solid var(--navy);background:#fff;color:var(--navy);font-size:13px;font-weight:700;text-align:center;line-height:12px;padding-top:8px}
.card-badge.light{background:var(--sky);border-color:#8cc5ef;color:#fff}
.card-note{position:absolute;left:50px;top:72px;font-size:12px;line-height:21px;color:var(--blue)}

.pager{position:absolute;left:748px;top:654px;height:23px;display:flex;border:1px solid #ccc;background:#fff;font-size:11px;color:var(--blue)}
.pager span{display:flex;align-items:center;justify-content:center;width:23px;border-left:1px solid #ccc;font-size:12px;font-weight:600}
.pager .prev{width:100px;border-left:0;font-size:8px;font-weight:400;color:var(--muted)}
.pager .next{width:100px;font-size:10px;font-weight:500}
.pager .current{background:var(--blue);color:#fff}
.pager .gap{width:24px}

.site-footer{position:absolute;left:0;top:728px;width:1200px;height:44px;background:var(--footer);color:#fff;font-size:12px;font-weight:500;display:flex;align-items:center;justify-content:center}
.site-footer .code{position:absolute;right:28px}
</style>
</head>
<body>

<header class="site-header">
  <a class="brand" href="http://velqoranthe.com/"><span class="brand-dot"></span><span class="brand-name">Velqoranthe</span></a>
  <nav class="header-icons">
    <svg viewBox="0 0 20 20"><circle cx="10" cy="10" r="9"/><rect x="9" y="8" width="2" height="7" fill="#fff"/><circle cx="10" cy="5.5" r="1.3" fill="#fff"/></svg>
    <svg viewBox="0 0 20 20"><circle cx="10" cy="6" r="4.5"/><path d="M2 19c0-5 3.5-7.5 8-7.5s8 2.5 8 7.5z"/></svg>
    <svg viewBox="0 0 20 20"><rect x="1" y="3" width="18" height="2.4"/><rect x="6" y="7.2" width="13" height="2.4"/><rect x="6" y="11.4" width="13" height="2.4"/><rect x="1" y="15.6" width="18" height="2.4"/></svg>
  </nav>
</header>

<section class="stats-panel">
  <div class="stats-deco" role="img" aria-label="Faint gear decoration"></div>
  <h2 class="stats-title">14&nbsp; Active Processes</h2>
  <svg class="donut" viewBox="0 0 104 104">
    <circle cx="52" cy="52" r="45" fill="none" stroke="var(--sky)" stroke-width="10"/>
    <circle cx="52" cy="52" r="45" fill="none" stroke="var(--navy)" stroke-width="10" stroke-dasharray="203.6 282.7" transform="rotate(-90 52 52)"/>
  </svg>
  <div class="donut-label">72%</div>
  <div class="stat-lines">
    <p>31 Millions Expent</p>
    <p>With 2 Millions Of Gap</p>
    <p>And 1.5 Million Negotiated</p>
  </div>
  <div class="stat-bar bar-spent"></div>
  <div class="stat-bar bar-gap"><span>6%</span></div>
  <div class="stat-bar bar-negotiated"><span>5%</span></div>
</section>

<section class="feed-panel">
  <h2 class="feed-head"><svg viewBox="0 0 20 16"><rect width="20" height="2.5"/><rect x="5" y="4.5" width="15" height="2.5"/><rect x="5" y="9" width="15" height="2.5"/><rect y="13.5" width="20" height="2.5"/></svg>Activity Feed</h2>
  <svg class="feed-icon" style="top:110px" viewBox="0 0 32 32"><circle cx="16" cy="16" r="14" fill="none" stroke="var(--coral)" stroke-width="2.5"/><circle cx="16" cy="16" r="8.5" fill="none" stroke="var(--coral)" stroke-width="2.5"/><circle cx="16" cy="16" r="3.5" fill="var(--coral)"/></svg>
  <p class="feed-text" style="top:95px">Tavik Orlen upload new data with 23823 rows to the XPTO Process and he is happy now - 2 days ago</p>
  <svg class="feed-icon" style="top:190px" viewBox="0 0 32 32"><path d="M16 2l13 6v16l-13 6-13-6V8z" fill="var(--coral)"/><path d="M3 8l13 6 13-6M16 14v16" stroke="#f2f2f2" stroke-width="2" fill="none"/></svg>
  <p class="feed-text" style="top:181px">Mirel Dant started the ABC process<br>- 2 days ago</p>
  <svg class="feed-icon" style="top:258px" viewBox="0 0 32 32"><path d="M7 3h13l6 6v20H7z" fill="var(--coral)"/><path d="M20 3v6h6" fill="none" stroke="#f2f2f2" stroke-width="2"/><path d="M11 15h11M11 20h11M11 25h7" stroke="#f2f2f2" stroke-width="2"/></svg>
  <p class="feed-text" style="top:248px">Orsa Quillen is making a new content layout specification - 2 days ago</p>
  <a class="see-all" href="#">see all</a>
</section>

<nav class="toolbar">
  <span>Search</span><span>Sort By</span><span>Filter By</span><span>Add Proceess</span>
</nav>

<section class="cards-panel">
  <article class="process-card" style="left:21px;top:40px">
    <div class="card-media" role="img" aria-label="Wooden deck chairs facing a lake"><svg class="card-flag" viewBox="0 0 44 44"><path d="M0 0h44v44z" fill="var(--coral)"/><path d="M26 13l4 4 8-8" stroke="#fff" stroke-width="3" fill="none"/></svg><h3 class="card-title">PROCESS BUY A DONUT</h3></div>
    <div class="card-body"><svg class="card-arrow" viewBox="0 0 16 16"><path d="M8 1l7 7-7 7-2-2 3.5-3.5H1v-3h8.5L6 3z"/></svg><p class="card-amount">14 million<small>In Expenses</small></p><div class="card-badge">$<br>234</div><p class="card-note">Some short free text with<br>links and 13,432 numbers</p></div>
  </article>
  <article class="process-card" style="left:303px;top:41px">
    <div class="card-media" role="img" aria-label="Wooden deck chairs facing a lake"><svg class="card-flag" viewBox="0 0 44 44"><path d="M0 0h44v44z" fill="var(--coral)"/><path d="M26 13l4 4 8-8" stroke="#fff" stroke-width="3" fill="none"/></svg><h3 class="card-title">PROCESS BUY A DONUT</h3></div>
    <div class="card-body"><svg class="card-arrow" viewBox="0 0 16 16" style="fill:var(--sky)"><path d="M8 1l7 7-7 7-2-2 3.5-3.5H1v-3h8.5L6 3z"/></svg><p class="card-amount">14 million<small>In Expenses</small></p><div class="card-badge light">$<br>234</div><p class="card-note">Some short free text with<br>links and 13,432 numbers</p></div>
  </article>
  <article class="process-card" style="left:19px;top:266px">
    <div class="card-media" role="img" aria-label="Wooden deck chairs facing a lake"><svg class="card-flag" viewBox="0 0 44 44"><path d="M0 0h44v44z" fill="var(--coral)"/><path d="M26 13l4 4 8-8" stroke="#fff" stroke-width="3" fill="none"/></svg><h3 class="card-title">PROCESS BUY A DONUT</h3></div>
    <div class="card-body"><svg class="card-arrow" viewBox="0 0 16 16" style="fill:var(--sky)"><path d="M8 1l7 7-7 7-2-2 3.5-3.5H1v-3h8.5L6 3z"/></svg><p class="card-amount">14 million<small>In Expenses</small></p><div class="card-badge light">$<br>234</div><p class="card-note">Some short free text with<br>links and 13,432 numbers</p></div>
  </article>
  <article class="process-card" style="left:304px;top:268px">
    <div class="card-media" role="img" aria-label="Wooden deck chairs facing a lake"><svg class="card-flag" viewBox="0 0 44 44"><path d="M0 0h44v44z" fill="var(--coral)"/><path d="M26 13l4 4 8-8" stroke="#fff" stroke-width="3" fill="none"/></svg><h3 class="card-title">PROCESS BUY A DONUT</h3></div>
    <div class="card-body"><svg class="card-arrow" viewBox="0 0 16 16" style="fill:var(--navy)"><path d="M8 1l7 7-7 7-2-2 3.5-3.5H1v-3h8.5L6 3z"/></svg><p class="card-amount">14 million<small>In Expenses</small></p><div class="card-badge">$<br>234</div><p class="card-note">Some short free text with<br>links and 13,432 numbers</p></div>
  </article>
</section>

<nav class="pager">
  <span class="prev">Previous Page</span>
  <span class="current">1</span><span>2</span><span>3</span><span>4</span><span class="gap">....</span>
  <span class="next">Next Page</span>
</nav>

<footer class="site-footer">
  <p>© Velqoranthe Partners2017. All Rights Reserved.</p>
  <span class="code">C12</span>
</footer>

</body>
</html>
```